Lumen Harbor is a Smart Device and Wiring Business offering the latest in Smart Home Devices inc

Looking for a new website to draw people to my business and explain what a smart home is all about. I currently own a domain and have a website I put together in webquill business website builder. address www.lumenharbor.example. The website needs modernising and be visually appealing with cool action buttons, client feedback page etc.

The webpage needs to present an image of seamless integration of wireless voice control and smart devices that take tasks and activities away from the owner saving them time and money.

I have a facebook business page(lumen harbor) and instagram linked with the business, are we able to link this to the website somehow?

Target Market(s)

Residential home owners who want to modernise their home. Who have seen adverts for corvo hub and pellar mira and want to put it in their home.

Industry/Entity Type

Technology Equipment

Number of Pages Required

1 page

Colors

Designer to choose colors to be used in the design.

Requirements
Must have
• A great landing page, that is modern and attractive, that gets across the idea of smart devices and technology.
• Must be ios/android device friendly.
Nice to have
• interactive/animated buttons
• I like the direction and interactiveness of these websites, a simplified version would be awesome.
• Something in between:
• http://www.quorbeliving.example/ and https://plindo.example/
• http://www.quorbeliving.example/

```html
<!DOCTYPE html>
<html lang="en">
<head>
<meta charset="utf-8">
<title>Lumen Harbor – Smart Device Integration</title>
<link rel="stylesheet" href="https://fonts.googleapis.com/css2?family=Lato:wght@400;700&family=Open+Sans:ital,wght@0,400;0,600;1,400&display=swap">
<style>
  :root{
    --blue:#1c74bb;
    --blue-deep:#1a5a9e;
    --teal:#2d9cc5;
    --teal-text:#2b8fb8;
    --ink:#1d1d1d;
    --body:#555b60;
    --muted:#8a8f94;
    --white:#ffffff;
    --grey-bg:#ececec;
    --hero-dark:#2b2a28;
  }
  *{box-sizing:border-box;margin:0;padding:0}
  html,body{width:1200px;height:3396px;overflow:hidden;background:var(--white)}
  body{position:relative;font-family:"Open Sans",Arial,sans-serif;color:var(--body)}
  .abs{position:absolute}
  .heading{font-family:"Lato",Arial,sans-serif}

  /* Header */
  .site-header{left:0;top:0;width:1200px;height:102px;background:var(--white)}
  .brand{left:126px;top:26px;display:flex;align-items:center;gap:14px}
  .brand-dot{width:50px;height:50px;border-radius:50%;background:var(--blue)}
  .brand-name{font-family:"Lato",sans-serif;font-weight:700;font-size:30px;color:var(--ink);letter-spacing:1px}
  .main-nav{right:128px;top:40px;display:flex;gap:40px;font-family:"Lato",sans-serif;font-size:17px;color:var(--ink)}
  .main-nav .active{color:var(--blue)}

  /* Hero */
  .hero{left:0;top:102px;width:1200px;height:690px;overflow:hidden}
  .hero-photo{position:absolute;inset:0;background:linear-gradient(160deg,#6b6560 0%,#3b3834 45%,#2a2826 70%,#4d4843 100%)}
  .hero-play{left:564px;top:178px;width:80px;height:80px;border-radius:50%;border:4px solid var(--white);background:rgba(0,0,0,.35)}
  .hero-title{left:0;top:278px;width:1200px;text-align:center;font-family:"Lato",sans-serif;font-weight:700;font-size:42px;color:var(--white);letter-spacing:.5px}
  .hero-sub{left:0;top:342px;width:1200px;text-align:center;font-family:"Lato",sans-serif;font-size:20px;line-height:29px;color:var(--white)}
  .hero-curve{left:0;top:690px;width:1200px}

  /* What we do */
  .section-title{width:1200px;left:0;text-align:center;font-family:"Lato",sans-serif;font-weight:700;font-size:28px;color:var(--ink);letter-spacing:.5px}
  .service-card{top:856px;width:215px;height:317px;background:var(--white);box-shadow:0 4px 18px rgba(0,0,0,.16);text-align:center}
  .service-card svg{margin-top:30px}
  .service-name{margin-top:12px;font-family:"Lato",sans-serif;font-weight:700;font-size:16px;line-height:20px;color:var(--blue)}
  .service-text{margin:14px 24px 0;font-size:12px;line-height:21px;color:var(--body)}
  .btn-outline{display:inline-block;border:2px solid var(--blue);color:var(--blue);font-family:"Lato",sans-serif;font-weight:700;font-size:12px;letter-spacing:.5px}
  .service-card .btn-outline{margin-top:16px;width:126px;height:36px;line-height:32px}

  /* Why choose us */
  .why{left:0;top:1259px;width:1200px;height:496px;overflow:hidden}
  .why-photo{position:absolute;inset:0;background:linear-gradient(120deg,#d9d3cc 0%,#b8a596 45%,#5f6a78 75%,#3a4454 100%)}
  .why-blue{position:absolute;left:0;top:0}
  .why-title{left:150px;top:99px;font-family:"Lato",sans-serif;font-size:28px;color:var(--white);letter-spacing:.5px}
  .why-text{left:150px;width:400px;font-size:14.5px;line-height:25px;color:var(--white)}
  .btn-light{left:150px;top:344px;width:140px;height:38px;line-height:34px;text-align:center;border:2px solid var(--white);color:var(--white);font-family:"Lato",sans-serif;font-weight:700;font-size:12px}

  /* Smart devices */
  .devices{left:0;top:1755px;width:1200px;height:516px;background:linear-gradient(180deg,#f4f4f4 0%,#e2e2e2 100%);overflow:hidden}
  .device-photo{left:188px;top:147px;width:367px;height:267px;border-radius:6px;background:linear-gradient(90deg,#1e1e1e 0%,#3a3a3a 30%,#9a9a9a 55%,#e2e2e2 85%,#f2f2f2 100%)}
  .device-name{left:611px;top:150px;font-family:"Lato",sans-serif;font-size:33px;color:var(--blue)}
  .device-text{left:611px;top:208px;width:430px;font-size:15px;line-height:27px;color:var(--body)}
  .devices .btn-outline{position:absolute;left:611px;top:330px;width:146px;height:40px;line-height:36px;text-align:center}
  .ridge{left:0;bottom:0}

  /* Testimonials */
  .testimonials-title{left:0;top:2316px;width:1200px;text-align:center;font-family:"Lato",sans-serif;font-size:37px;color:var(--teal-text)}
  .quote-card{top:2400px;width:294px;height:185px;background:var(--white);box-shadow:0 4px 16px rgba(0,0,0,.14);padding:28px 24px 0 56px}
  .quote-mark{position:absolute;left:20px;top:22px;font-family:"Lato",sans-serif;font-weight:700;font-size:48px;line-height:48px;color:var(--teal)}
  .quote-text{font-style:italic;font-size:12.5px;line-height:24px;color:var(--muted)}
  .author{top:2603px;display:flex;align-items:center;gap:14px}
  .avatar{width:48px;height:48px;border-radius:50%;background:linear-gradient(180deg,#b59a84,#5a4a3e)}
  .author-name{font-family:"Lato",sans-serif;font-size:15px;color:var(--ink)}
  .author-city{font-size:12px;color:var(--muted);margin-top:2px}

  /* Contact */
  .contact{left:0;top:2757px;width:600px;height:458px;background:var(--teal)}
  .contact-photo{left:600px;top:2757px;width:600px;height:458px;background:linear-gradient(170deg,#e9e9e9 0%,#cfcfcf 45%,#6b4a32 75%,#3d2a1c 100%)}
  .contact-title{left:116px;top:56px;font-family:"Lato",sans-serif;font-size:33px;color:var(--white)}
  .field{left:116px;width:415px;border-bottom:2px solid rgba(255,255,255,.85);font-family:"Lato",sans-serif;font-size:15px;color:var(--white);padding-bottom:10px}
  .btn-send{left:412px;top:370px;width:119px;height:38px;line-height:38px;border-radius:20px;background:var(--blue-deep);color:var(--white);text-align:center;font-family:"Lato",sans-serif;font-size:15px}

  /* Footer */
  .footer-nav{left:0;top:3255px;width:1200px;display:flex;justify-content:center;gap:40px;font-family:"Lato",sans-serif;font-size:15px;color:var(--ink)}
  .copyright{left:0;top:3288px;width:1200px;text-align:center;font-size:13px;color:var(--body)}
  .social{left:0;top:3326px;width:1200px;display:flex;justify-content:center;gap:6px}
  .social span{width:31px;height:31px;border-radius:50%;border:2px solid var(--blue)}
</style>
</head>
<body>

<header class="site-header abs">
  <div class="brand abs"><span class="brand-dot"></span><span class="brand-name">Lumen Harbor</span></div>
  <nav class="main-nav abs">
    <span class="active">HOME</span><span>WHAT WE DO</span><span>PRODUCTS</span><span>ABOUT US</span><span>CONTACT US</span>
  </nav>
</header>

<section class="hero abs">
  <div class="hero-photo" role="img" aria-label="Modern kitchen with a wall-mounted smart home control panel"></div>
  <div class="hero-play abs">
    <svg width="72" height="72" viewBox="0 0 72 72"><polygon points="29,22 29,50 51,36" fill="#fff"/></svg>
  </div>
  <h1 class="hero-title abs">SMART DEVICE INTEGRATION</h1>
  <p class="hero-sub abs">WE ARE FOCUSED ON DELIVERING AFFORDABLE AND EASILY USABLE<br>DEVICES FOR YOUR HOME AND OFFICE</p>
</section>
<svg class="hero-curve abs" style="top:702px" width="1200" height="100" viewBox="0 0 1200 100">
  <path d="M0 90 Q600 -40 1200 40 L1200 100 L0 100 Z" fill="#1c74bb"/>
  <path d="M0 100 Q600 -20 1200 56 L1200 100 Z" fill="#fff"/>
</svg>

<h2 class="section-title abs" style="top:783px">WHAT WE DO</h2>

<article class="service-card abs" style="left:129px">
  <svg width="70" height="66" viewBox="0 0 70 66" fill="none" stroke="#1c74bb" stroke-width="3"><path d="M8 30 L35 6 L62 30 M14 25 V60 H56 V25"/><rect x="38" y="36" width="12" height="20" rx="3"/></svg>
  <div class="service-name">HOME<br>AUTOMATION</div>
  <p class="service-text">Morbi diam mauris viverra in gravida eu mattis in ante Morbi eget arcu Morbi</p>
  <span class="btn-outline">READ MORE</span>
</article>
<article class="service-card abs" style="left:369px">
  <svg width="100" height="66" viewBox="0 0 100 66"><rect x="4" y="12" width="26" height="46" fill="#1c74bb"/><rect x="70" y="12" width="26" height="46" fill="#1c74bb"/><rect x="34" y="26" width="32" height="32" fill="#1c74bb"/><circle cx="17" cy="42" r="8" fill="#fff"/><circle cx="83" cy="42" r="8" fill="#fff"/><circle cx="17" cy="24" r="4" fill="#fff"/><circle cx="83" cy="24" r="4" fill="#fff"/></svg>
  <div class="service-name">HOME<br>THEATRE DESIGN</div>
  <p class="service-text">Morbi diam mauris viverra in gravida eu mattis in ante Morbi eget arcu Morbi</p>
  <span class="btn-outline">READ MORE</span>
</article>
<article class="service-card abs" style="left:611px">
  <svg width="70" height="66" viewBox="0 0 70 66" fill="none" stroke="#1c74bb" stroke-width="3"><rect x="14" y="4" width="18" height="56" rx="6"/><ellipse cx="50" cy="46" rx="13" ry="5"/><path d="M37 46 V56 Q50 64 63 56 V46"/></svg>
  <div class="service-name">MEDIA<br>ENTERTAINMENT</div>
  <p class="service-text">Morbi diam mauris viverra in gravida eu mattis in ante Morbi eget arcu Morbi</p>
  <span class="btn-outline">READ MORE</span>
</article>
<article class="service-card abs" style="left:851px">
  <svg width="70" height="66" viewBox="0 0 70 66" fill="none" stroke="#1c74bb" stroke-width="3"><rect x="18" y="2" width="34" height="56" rx="3"/><circle cx="35" cy="34" r="11"/><circle cx="35" cy="34" r="4"/><circle cx="35" cy="13" r="3"/><path d="M22 64 H48"/></svg>
  <div class="service-name">MULTI ROOM<br>AUDIO</div>
  <p class="service-text">Morbi diam mauris viverra in gravida eu mattis in ante Morbi eget arcu Morbi</p>
  <span class="btn-outline">READ MORE</span>
</article>

<section class="why abs">
  <div class="why-photo" role="img" aria-label="Couple on a sofa looking at a tablet together"></div>
  <svg class="why-blue" width="700" height="496" viewBox="0 0 700 496">
    <defs><linearGradient id="whyGrad" x1="0" y1="0" x2="1" y2="1"><stop offset="0" stop-color="#1f63a8"/><stop offset="1" stop-color="#1b7cc4"/></linearGradient></defs>
    <polygon points="0,0 680,0 482,496 0,496" fill="url(#whyGrad)"/>
  </svg>
  <h2 class="why-title abs">WHY CHOOSE US</h2>
  <p class="why-text abs" style="top:157px">Aaculis ipsum dui aliquet felis at cursus magna nisl nec elit Praesent elementum elit at tellus nec</p>
  <p class="why-text abs" style="top:222px">Altricies sit amet porttitor mattis enim In massa libero interdum nec interdum vel blandit sed nulla In ullamcor-per est eget tempor cursus neque mi consectetuer mi a ultricies massa est sed nisl Class aptent t</p>
  <span class="btn-light abs">READ MORE</span>
</section>

<section class="devices abs">
  <h2 class="section-title abs" style="top:55px;color:#2a1f33">SMART DEVICES</h2>
  <div class="device-photo abs" role="img" aria-label="Three cylindrical smart speakers in black, silver and white"></div>
  <h3 class="device-name abs">Orvia Speaker</h3>
  <p class="device-text abs">Altricies sit amet porttitor mattis enim In massa libero interdum nec interdum vel blandit sed nulla In ullamcor-per est eget tempor cursus neque mi consectetuer mi a ultricies massa est sed nisl Class aptent t</p>
  <span class="btn-outline">READ MORE</span>
  <svg class="ridge abs" width="1200" height="80" viewBox="0 0 1200 80">
    <path d="M0 80 L0 60 L160 52 L300 72 L420 50 L520 60 L600 6 L700 50 L800 44 L880 56 L1000 40 L1100 58 L1200 50 L1200 80 Z" fill="#fff"/>
  </svg>
</section>

<h2 class="testimonials-title abs">Testimonials</h2>

<blockquote class="quote-card abs" style="left:120px"><span class="quote-mark">“</span><p class="quote-text">Morbi diam mauris viverra in gravida eu mattis in ante Morbi eget arcu Morbi porta libero id ullamcorper nonummy nibh ligula pulvinar metus eget</p></blockquote>
<blockquote class="quote-card abs" style="left:453px"><span class="quote-mark">“</span><p class="quote-text">Morbi diam mauris viverra in gravida eu mattis in ante Morbi eget arcu Morbi porta libero id ullamcorper nonummy nibh ligula pulvinar metus eget</p></blockquote>
<blockquote class="quote-card abs" style="left:788px"><span class="quote-mark">“</span><p class="quote-text">Morbi diam mauris viverra in gravida eu mattis in ante Morbi eget arcu Morbi porta libero id ullamcorper nonummy nibh ligula pulvinar metus eget</p></blockquote>

<div class="author abs" style="left:130px"><span class="avatar" role="img" aria-label="Client portrait"></span><div><div class="author-name">By Author Name</div><div class="author-city">City Location</div></div></div>
<div class="author abs" style="left:463px"><span class="avatar" role="img" aria-label="Client portrait"></span><div><div class="author-name">By Author Name</div><div class="author-city">City Location</div></div></div>
<div class="author abs" style="left:798px"><span class="avatar" role="img" aria-label="Client portrait"></span><div><div class="author-name">By Author Name</div><div class="author-city">City Location</div></div></div>

<section class="contact abs">
  <h2 class="contact-title abs">Contact Us</h2>
  <div class="field abs" style="top:126px">Name</div>
  <div class="field abs" style="top:177px">Email</div>
  <div class="field abs" style="top:230px;height:130px">Message</div>
  <span class="btn-send abs">Contact Us</span>
</section>
<div class="contact-photo abs" role="img" aria-label="Living room with wall-mounted TV, speakers and wooden floor"></div>

<footer>
  <nav class="footer-nav abs"><span>HOME</span><span>WHAT WE DO</span><span>PRODUCTS</span><span>ABOUT US</span><span>CONTACT US</span></nav>
  <p class="copyright abs">© 2018 Company Name&nbsp; All right reserved</p>
  <div class="social abs"><span></span><span></span><span></span><span></span></div>
</footer>

</body>
</html>
```